Business Card for Polygraph business in Africa

Business Card . Polygraph Examiner based in Tanzania, East Africa.
Business Card will be used to disseminate contact information to potential clients.
It should convey that I am a professional specifically in the polygraph field and perform my work with integrity.

I have attached the business card that I'm currently using, which I threw together myself initially. It's not professional enough.

Target Market(s)

Banks, Accounting Firms, Government Ministries, Gas, Oil, & Gemstone Mining Concerns, Wildlife Conservation NGOs, International companies located in East Africa.

Industry/Entity Type

Business

Contact Information for Business Card

Veritrace Kilonga
Miriam Holloway
PO Box 48317
Arusha, Tanzania
+255 612 839 274
miriamholloway@postvale.example

Colors
00a990
f37122
faa54b

Requirements
Must have
• - Veritrace Kilonga (with the word "Polygraph" being more prominent than the word "Tanzania")
• - Forensic Examinations
• - Employment Screening
• - Should contain a logo of the Continental Truthline Society (of which I'm a member)
• - I would like an accent design (such as the polygraph "squiggles" of a cardio tracing or such as that)
• - My contact information (less prominent, but large enough to read legibly). I would also consider putting the contact information on the second side of the card.
Nice to have
• My color suggestions are changeable.
Should not have
• Anything "cutesy" or "cartoonish"

```html
<!DOCTYPE html>
<html lang="en">
<head>
<meta charset="utf-8">
<title>Veritrace Kilonga – Business Card</title>
<link rel="stylesheet" href="https://fonts.googleapis.com/css2?family=Roboto:wght@400;500;700&family=Roboto+Condensed:wght@700&display=swap">
<style>
  :root {
    --backdrop: #2b2b2b;
    --card-white: #f3f3f3;
    --brand-blue: #0b4592;
    --logo-blue: #0a4aa0;
    --text-grey: #4a4a4a;
    --paper: #f5f5f5;
  }
  html, body {
    margin: 0;
    padding: 0;
    width: 1200px;
    height: 960px;
    overflow: hidden;
    background: var(--backdrop);
  }
  .canvas {
    position: relative;
    width: 1200px;
    height: 960px;
  }
  .card {
    position: absolute;
    left: 320px;
    width: 600px;
    border-radius: 16px;
    overflow: hidden;
  }
  .card-front {
    top: 100px;
    height: 350px;
    background: var(--card-white);
  }
  .brand {
    position: absolute;
    left: 0;
    right: 0;
    top: 150px;
    display: flex;
    align-items: center;
    justify-content: center;
    gap: 14px;
  }
  .brand-dot {
    width: 34px;
    height: 34px;
    border-radius: 50%;
    background: var(--logo-blue);
  }
  .brand-name {
    font-family: "Roboto", sans-serif;
    font-weight: 700;
    font-size: 38px;
    color: var(--logo-blue);
    letter-spacing: 0.5px;
  }
  .services {
    position: absolute;
    left: 0;
    right: 0;
    top: 296px;
    margin: 0;
    text-align: center;
    font-family: "Roboto", sans-serif;
    font-size: 14.5px;
    line-height: 20px;
    color: var(--text-grey);
  }
  .services .sep {
    display: inline-block;
    width: 7px;
    height: 7px;
    border-radius: 50%;
    background: var(--logo-blue);
    margin: 0 8px;
    vertical-align: middle;
  }
  .card-back {
    top: 493px;
    height: 342px;
    background: var(--brand-blue);
  }
  .member-badge {
    position: absolute;
    left: 26px;
    top: 24px;
    width: 72px;
    height: 72px;
    border-radius: 50%;
    background: var(--paper);
  }
  .baseline {
    position: absolute;
    top: 192px;
    height: 21px;
    background: var(--paper);
  }
  .baseline-left { left: 0; width: 118px; }
  .baseline-right { left: 282px; right: 0; }
  .tracing-area {
    position: absolute;
    left: 118px;
    top: 14px;
    width: 164px;
    height: 316px;
    border-radius: 10px;
    background: linear-gradient(180deg, rgba(245,245,245,0.30), rgba(245,245,245,0.12));
  }
  .holder {
    position: absolute;
    right: 28px;
    top: 66px;
    text-align: right;
    color: var(--paper);
  }
  .holder-name {
    font-family: "Roboto Condensed", sans-serif;
    font-weight: 700;
    font-size: 21px;
    letter-spacing: 0.3px;
    margin: 0;
    line-height: 1.1;
  }
  .holder-firm {
    font-family: "Roboto", sans-serif;
    font-weight: 500;
    font-size: 14.5px;
    letter-spacing: 0.5px;
    margin: 6px 0 0;
  }
  .contact {
    position: absolute;
    right: 28px;
    top: 248px;
    list-style: none;
    margin: 0;
    padding: 0;
    font-family: "Roboto", sans-serif;
    font-size: 14.5px;
    color: var(--paper);
    text-align: right;
    line-height: 21px;
  }
  .contact li {
    display: flex;
    justify-content: flex-end;
    align-items: center;
    gap: 7px;
  }
  .contact svg { width: 13px; height: 13px; }
</style>
</head>
<body>
<main class="canvas">

  <section class="card card-front" aria-label="Card front">
    <div class="brand">
      <span class="brand-dot"></span>
      <span class="brand-name">Veritrace Kilonga</span>
    </div>
    <p class="services">Forensic Examinations<span class="sep"></span>Employment Screening</p>
  </section>

  <section class="card card-back" aria-label="Card back">
    <div class="baseline baseline-left"></div>
    <div class="baseline baseline-right"></div>
    <div class="tracing-area" role="img" aria-label="Accent tracing of a polygraph chart peak rising from the white baseline"></div>
    <div class="member-badge" role="img" aria-label="Continental Truthline Society membership badge"></div>

    <div class="holder">
      <p class="holder-name">MIRIAM HOLLOWAY</p>
      <p class="holder-firm">VERITRACE KILONGA</p>
    </div>

    <ul class="contact">
      <li>+255 612 839 274
        <svg viewBox="0 0 24 24" aria-hidden="true"><path fill="#f5f5f5" d="M6.6 10.8a15.1 15.1 0 0 0 6.6 6.6l2.2-2.2c.3-.3.7-.4 1-.2 1.1.4 2.3.6 3.6.6.6 0 1 .4 1 1V20c0 .6-.4 1-1 1A17 17 0 0 1 3 4c0-.6.4-1 1-1h3.5c.6 0 1 .4 1 1 0 1.3.2 2.5.6 3.6.1.3 0 .7-.2 1z"/></svg>
      </li>
      <li>miriamholloway@postvale.example
        <svg viewBox="0 0 24 24" aria-hidden="true"><rect x="2" y="5" width="20" height="14" fill="#f5f5f5"/><polyline points="2,5 12,13 22,5" fill="none" stroke="#0b4592" stroke-width="2"/></svg>
      </li>
      <li>PO Box 48317, Arusha, Tanzania</li>
    </ul>
  </section>

</main>
</body>
</html>
```